Brightmill Data Works

Our company is about IT hardwares and IT solutions. IT hardware such as PC, RAMS, storage and servers. IT solutions such as project management, BA. We are also selling new technology too.

Target Market(s)

Consumer, Small to Medium Business, Corporate

Requirements
Must have
• The business card must have the following:
• Name:
• Title:
• Contact Number:
• Email address:
• Website:
• Color: Must match the logo color upgrade

```html
<!DOCTYPE html>
<html lang="en">
<head>
<meta charset="utf-8">
<title>Brightmill Data Works — Business Card</title>
<link rel="stylesheet" href="https://fonts.googleapis.com/css2?family=Open+Sans:wght@400;600&display=swap">
<style>
  :root {
    --backdrop: #2a2a2a;
    --card-grey: #4a4a4b;
    --gold: #e3a03a;
    --edge: #b8862f;
  }
  * { box-sizing: border-box; margin: 0; padding: 0; }
  html, body {
    width: 1200px;
    height: 900px;
    overflow: hidden;
    background: var(--backdrop);
    font-family: "Open Sans", Arial, sans-serif;
  }
  .canvas {
    position: relative;
    width: 1200px;
    height: 900px;
  }
  .card {
    position: absolute;
    width: 520px;
    height: 300px;
    background: var(--card-grey);
    border: 1px solid var(--edge);
    border-radius: 8px;
    overflow: hidden;
    box-shadow: 0 18px 40px rgba(0, 0, 0, 0.55);
    color: var(--gold);
  }
  .card--front { left: 80px; top: 110px; }
  .card--back  { left: 600px; top: 490px; }

  .accent-band {
    position: absolute;
    left: 0;
    right: 0;
    height: 12px;
    background: var(--gold);
  }
  .card--front .accent-band { bottom: 46px; }
  .card--back  .accent-band { bottom: 40px; }

  .brand {
    position: absolute;
    left: 0;
    right: 0;
    display: flex;
    align-items: center;
    justify-content: center;
    gap: 12px;
  }
  .brand__mark {
    background: var(--gold);
    border-radius: 50%;
  }
  .brand__name {
    font-weight: 600;
    color: var(--gold);
    letter-spacing: 0.04em;
    white-space: nowrap;
  }

  .card--front .brand { top: 104px; }
  .card--front .brand__mark { width: 30px; height: 30px; }
  .card--front .brand__name { font-size: 30px; }

  .card--back .brand { top: 34px; gap: 9px; }
  .card--back .brand__mark { width: 20px; height: 20px; }
  .card--back .brand__name { font-size: 20px; }

  .contact-list {
    position: absolute;
    top: 86px;
    left: 0;
    right: 0;
    list-style: none;
    text-align: center;
    font-size: 15px;
    line-height: 1.35;
  }
  .website {
    position: absolute;
    left: 0;
    right: 0;
    bottom: 58px;
    text-align: center;
    font-size: 15px;
  }
</style>
</head>
<body>
<main class="canvas">
  <section class="card card--front" aria-label="Card front">
    <div class="brand">
      <span class="brand__mark"></span>
      <span class="brand__name">Brightmill Data Works</span>
    </div>
    <div class="accent-band"></div>
  </section>

  <section class="card card--back" aria-label="Card back">
    <div class="brand">
      <span class="brand__mark"></span>
      <span class="brand__name">Brightmill Data Works</span>
    </div>
    <ul class="contact-list">
      <li>Name</li>
      <li>Title</li>
      <li>Contact Number</li>
      <li>Email address</li>
    </ul>
    <p class="website">Website</p>
    <div class="accent-band"></div>
  </section>
</main>
</body>
</html>
```